New design for Giftwell Hub Website - landing page plus 3 carousel pages

We have a new website we want to launch for 501c3 organizations - Faith-based organizations, not for profit organizations, colleges and universities. Note - this is a design only project. We want to see designs for the landing page and the 3 other pages - Faith-based organizations, not for profit organizations, colleges and universities.
Format: We expect to create this website in Wix so requirement is to make the graphics Wix compatible
See Dossier attached for more details, 4 wireframes (1 landing page and 3 carousel pages), and brand guidelines
Please be creative and and make the visuals engaging. We do NOT want you to simply replicate what is in the wireframe. We are looking for a totally new, fresh and engaging design.
Number of Pages Required
1 page
Look and feel
Each slider illustrates characteristics of the customer's brand and the style your logo design should communicate.

```html
<!DOCTYPE html>
<html lang="en">
<head>
<meta charset="utf-8">
<title>Giftwell Hub – 501C3 Organization</title>
<link href="https://fonts.googleapis.com/css2?family=Poppins:wght@400;500;600;700&display=swap" rel="stylesheet">
<style>
:root{
  --green:#17c08f;
  --green-dark:#0f9d76;
  --teal:#0a8f92;
  --navy:#0c1a3a;
  --ink:#0f1c33;
  --text:#555c66;
  --light:#f0f0f0;
  --blue:#4fa5e8;
  --yellow:#f6bd16;
  --red:#dd5349;
  --white:#fff;
}
*{box-sizing:border-box;margin:0;padding:0}
html,body{width:1200px;height:3830px;overflow:hidden;background:var(--white);font-family:"Poppins",sans-serif;color:var(--ink)}
.page{position:relative;width:1200px;height:3830px}
.abs{position:absolute}

/* header */
.hero{position:absolute;left:0;top:0;width:1200px;height:760px;background:radial-gradient(ellipse at 50% 30%,#fafafa 0%,#ececec 80%)}
.brand{position:absolute;left:110px;top:28px;display:flex;align-items:center;gap:12px;font-weight:600;font-size:28px;color:var(--navy)}
.brand-dot{width:40px;height:40px;border-radius:50%;border:5px solid var(--teal)}
.nav{position:absolute;left:400px;top:40px;display:flex;gap:22px;font-size:14px;font-weight:500;color:#222}
.nav .active{color:var(--green);border-bottom:2px solid var(--green);padding-bottom:4px}
.login{position:absolute;left:974px;top:28px;width:114px;height:42px;border-radius:21px;background:#fff;color:var(--green);font-size:14px;font-weight:500;display:flex;align-items:center;justify-content:center;box-shadow:0 2px 8px rgba(0,0,0,.06)}
.hero h1{position:absolute;left:0;width:1200px;top:232px;text-align:center;font-size:52px;font-weight:600;color:var(--navy)}
.hero .lead{position:absolute;left:290px;width:620px;top:312px;text-align:center;font-size:15px;line-height:26px;color:#444}
.segment{position:absolute;top:394px;width:142px;text-align:center}
.segment .ring{width:142px;height:142px;border-radius:50%;border:3px solid var(--teal);background:#fff;display:flex;align-items:center;justify-content:center}
.segment p{margin-top:8px;font-size:17px;line-height:26px;color:#fff;opacity:.9}
.wave{position:absolute;left:0;top:640px}

/* process */
.section-title{position:absolute;left:0;width:1200px;text-align:center;font-weight:600;color:var(--navy)}
.step{position:absolute;width:210px}
.step .circle{width:128px;height:128px;border-radius:50%;display:flex;align-items:center;justify-content:center}
.step .badge{display:inline-block;margin-top:16px;background:var(--green);color:#fff;font-size:13px;font-weight:600;padding:3px 18px;border-radius:14px}
.step p{margin-top:12px;font-size:15px;line-height:26px;color:var(--text)}
.btn{position:absolute;display:flex;align-items:center;justify-content:center;border-radius:24px;color:#fff;font-size:14px;font-weight:600;text-transform:uppercase}
.btn-teal{background:var(--teal)}
.btn-green{background:var(--green)}

/* donation */
.donation{position:absolute;left:0;top:1466px;width:1200px;height:540px;background:linear-gradient(90deg,#dfeee9 0%,var(--light) 25%,var(--light) 75%,#dfeee9 100%)}
.donation .sub{position:absolute;left:0;width:1200px;text-align:center;font-size:16px;font-weight:500}
.amounts{position:absolute;left:110px;top:241px;display:flex;gap:8px}
.amount{width:158px;height:74px;border:3px solid var(--green);background:#a9ecd7;color:var(--green-dark);font-size:36px;font-weight:600;display:flex;align-items:center;justify-content:center;border-radius:4px}
.amount.other{background:var(--green);color:#fff;font-size:15px;line-height:25px;text-align:center}
.cards{position:absolute;left:432px;top:342px;display:flex;gap:10px}
.pay{width:60px;height:34px;background:#fff;border:1px solid #ddd;border-radius:3px;display:flex;align-items:center;justify-content:center}
.pay span{width:28px;height:12px;border-radius:2px;background:#c9ced6}

/* cards */
.give-card{position:absolute;top:2110px;width:478px;height:410px;background:var(--navy);border-radius:4px;text-align:center;color:#fff}
.give-card .icon{width:116px;height:116px;border-radius:50%;background:#fff;margin:32px auto 0;display:flex;align-items:center;justify-content:center}
.give-card h3{margin-top:28px;font-size:17px;font-weight:600}
.give-card .pow{margin-top:6px;font-size:12px}
.give-card .mark{margin-top:14px;display:flex;align-items:center;justify-content:center;gap:12px;font-size:30px;font-weight:500}
.give-card .mark i{width:44px;height:44px;border-radius:50%;border:4px solid #fff}
.give-card .btn{position:relative;margin:22px auto 0;width:166px;height:44px}

/* video */
.video{position:absolute;left:111px;top:2623px;width:978px;height:428px;border-radius:10px;background:linear-gradient(135deg,#6e6a63 0%,#8c8579 40%,#4e4b47 100%);box-shadow:0 30px 30px -20px rgba(0,0,0,.35)}
.play{position:absolute;left:459px;top:184px;width:60px;height:60px;border-radius:50%;background:var(--green);display:flex;align-items:center;justify-content:center}

/* footer */
.enroll{position:absolute;left:0;top:3155px;width:597px;height:555px;background:var(--navy);color:#fff}
.notify{position:absolute;left:597px;top:3155px;width:603px;height:555px;background:var(--green);color:#fff}
.enroll h2{position:absolute;left:110px;top:72px;font-size:32px;font-weight:700}
.perk{position:absolute;left:110px;display:flex;gap:16px}
.perk .ic{width:78px;height:78px;border-radius:50%;background:var(--green);flex:none;display:flex;align-items:center;justify-content:center}
.perk h4{font-size:16px;font-weight:600;margin-top:0}
.perk p{font-size:15px;line-height:26px;margin-top:4px;width:340px}
.notify h2{position:absolute;left:83px;top:65px;font-size:33px;line-height:40px;font-weight:700}
.subscribe{position:absolute;left:83px;top:165px;width:442px;height:50px;border-radius:25px;background:#fff;display:flex;align-items:center;justify-content:space-between;padding-left:28px}
.subscribe span{font-size:14px;color:#555}
.subscribe b{height:44px;width:152px;margin-right:3px;border-radius:22px;background:var(--navy);color:#fff;font-size:14px;display:flex;align-items:center;justify-content:center}
.notify h3{position:absolute;left:83px;top:230px;font-size:33px;font-weight:400}
.notify p{position:absolute;left:83px;width:445px;font-size:14px;line-height:25px}
.copy{position:absolute;left:0;top:3754px;width:1200px;text-align:center;font-size:15px;color:#555}
</style>
</head>
<body>
<div class="page">

  <section class="hero">
    <div class="brand"><span class="brand-dot"></span>Giftwell Hub</div>
    <nav class="nav">
      <span class="active">HOME</span><span>ABOUT US</span><span>NEWSROOM</span><span>PATENTS</span><span>CLIENTS</span><span>FAQ</span><span>CONTACT</span>
    </nav>
    <div class="login">
      <svg width="12" height="12" viewBox="0 0 12 12"><circle cx="6" cy="3.5" r="3" fill="#17c08f"/><path d="M0 12c0-4 3-5.5 6-5.5s6 1.5 6 5.5z" fill="#17c08f"/></svg>&nbsp;LOGIN
    </div>
    <h1>501C3 ORGANIZATION</h1>
    <p class="lead">Lorem ipsum dolor sit amet, consectetur adipiscing elit, sed do eiusmod tempor incididunt ut labore et dolore magna aliqua</p>

    <div class="segment" style="left:294px">
      <div class="ring"><svg width="70" height="70" viewBox="0 0 70 70"><g fill="#17c08f"><path d="M35 5l10 15-10 10-10-10z"/><path d="M65 35l-15 10-10-10 10-10z"/><path d="M35 65l-10-15 10-10 10 10z"/><path d="M5 35l15-10 10 10-10 10z" fill="#0a8f92"/></g></svg></div>
      <p>Non Profit Organization</p>
    </div>
    <div class="segment" style="left:531px">
      <div class="ring"><svg width="96" height="96" viewBox="0 0 96 96"><circle cx="48" cy="48" r="46" fill="#0c1a3a"/><circle cx="48" cy="48" r="22" fill="#fff"/><path d="M48 2a46 46 0 0 1 46 46H70A22 22 0 0 0 48 26z" fill="#17c08f"/></svg></div>
      <p>Faith Based</p>
    </div>
    <div class="segment" style="left:765px">
      <div class="ring"><svg width="64" height="70" viewBox="0 0 64 70"><path d="M32 2l24 10-24 10L8 12z" fill="#0c1a3a"/><circle cx="32" cy="28" r="13" fill="#17c08f"/><path d="M4 70c0-18 12-26 28-26s28 8 28 26z" fill="#17c08f"/></svg></div>
      <p>Colleges and Universities</p>
    </div>

    <svg class="wave" width="1200" height="120" viewBox="0 0 1200 120">
      <path d="M0 0C250 70 450 95 700 90 900 85 1080 45 1200 10V120H0z" fill="#fff"/>
      <path d="M0 12C250 80 450 100 700 95 900 90 1080 55 1200 14" fill="none" stroke="url(#wg)" stroke-width="18"/>
      <defs><linearGradient id="wg" x1="0" x2="1"><stop offset="0" stop-color="#0a7d8f"/><stop offset="1" stop-color="#17c08f"/></linearGradient></defs>
    </svg>
  </section>

  <h2 class="section-title" style="top:845px;font-size:50px">OUR PROCESS</h2>
  <svg class="abs" style="left:85px;top:920px" width="960" height="170" viewBox="0 0 960 170">
    <path d="M5 5C20 60 60 70 90 85 150 130 200 160 280 160 350 150 380 60 560 65 620 90 640 140 770 150 860 150 940 80 955 60" fill="none" stroke="#0c1a3a" stroke-width="2.5" stroke-dasharray="5 6"/>
  </svg>
  <div class="step" style="left:111px;top:944px">
    <div class="circle" style="background:var(--green)"><svg width="64" height="64" viewBox="0 0 64 64" fill="none" stroke="#fff" stroke-width="3"><rect x="6" y="18" width="52" height="36" rx="3"/><circle cx="32" cy="36" r="9"/><path d="M16 18V6M32 18V6M48 18V6"/></svg></div>
    <span class="badge">STEP 1</span>
    <p>Lorem ipsum dolor sit amet, consectetur adipiscing elit, sed do eiusmod tempor inci didunt ut labore</p>
  </div>
  <div class="step" style="left:368px;top:996px">
    <div class="circle" style="background:var(--blue)"><svg width="64" height="64" viewBox="0 0 64 64" fill="none" stroke="#fff" stroke-width="3"><path d="M8 32h20M28 12v40M28 16h14M28 32h14M28 48h14"/><circle cx="50" cy="16" r="6"/><circle cx="50" cy="32" r="6"/><circle cx="50" cy="48" r="6"/></svg></div>
    <span class="badge">STEP 2</span>
    <p>Lorem ipsum dolor sit amet, consectetur adipiscing elit, sed do eiusmod tempor inci didunt ut labore</p>
  </div>
  <div class="step" style="left:625px;top:944px">
    <div class="circle" style="background:var(--yellow)"><svg width="64" height="64" viewBox="0 0 64 64" fill="none" stroke="#fff" stroke-width="3"><rect x="6" y="8" width="52" height="36" rx="3"/><path d="M24 56h16M32 44v12M14 18h20M14 26h14"/><circle cx="46" cy="32" r="8"/></svg></div>
    <span class="badge">STEP 3</span>
    <p>Lorem ipsum dolor sit amet, consectetur adipiscing elit, sed do eiusmod tempor inci didunt ut labore</p>
  </div>
  <div class="step" style="left:882px;top:996px">
    <div class="circle" style="background:var(--red)"><svg width="64" height="64" viewBox="0 0 64 64" fill="none" stroke="#fff" stroke-width="3"><rect x="4" y="8" width="46" height="34" rx="3"/><path d="M10 34l10-12 8 8 6-6 10 10"/><rect x="40" y="28" width="20" height="30" rx="3"/></svg></div>
    <span class="badge">STEP 4</span>
    <p>Lorem ipsum dolor sit amet, consectetur adipiscing elit, sed do eiusmod tempor inci didunt ut labore</p>
  </div>
  <div class="btn btn-teal" style="left:517px;top:1318px;width:166px;height:44px">Donate Data</div>

  <section class="donation">
    <h2 class="section-title" style="top:80px;font-size:50px">MY DONATION</h2>
    <p class="sub" style="top:156px;color:#333">ALL DONATION ARE TAX DEDUCTIBLE</p>
    <p class="sub" style="top:192px;color:var(--green)">I WANT TO GIVE</p>
    <div class="amounts">
      <div class="amount">$25</div><div class="amount">$50</div><div class="amount">$100</div><div class="amount">$125</div><div class="amount">$150</div><div class="amount other">OTHER<br>AMOUNT</div>
    </div>
    <div class="cards">
      <div class="pay"><span></span></div><div class="pay"><span></span></div><div class="pay"><span></span></div><div class="pay"><span></span></div><div class="pay"><span></span></div>
    </div>
    <div class="btn btn-teal" style="left:482px;top:400px;width:236px;height:44px;font-size:13px">Donate with credit card</div>
  </section>

  <div class="give-card" style="left:111px">
    <div class="icon"><svg width="60" height="60" viewBox="0 0 60 60" fill="none" stroke="#0a8f92" stroke-width="3"><rect x="10" y="18" width="40" height="30" rx="4"/><circle cx="30" cy="14" r="9"/><path d="M36 33h14"/></svg></div>
    <h3>DONATE WITH CRYPTO</h3>
    <p class="pow">POWERED BY GWH</p>
    <div class="mark"><i></i>Giftwell Hub</div>
    <div class="btn btn-green">Donate Data</div>
  </div>
  <div class="give-card" style="left:611px">
    <div class="icon"><svg width="60" height="60" viewBox="0 0 60 60" fill="none" stroke="#0a8f92" stroke-width="3"><circle cx="34" cy="24" r="18"/><path d="M20 38L6 54M26 30v-6M33 30V16M40 30v-10"/></svg></div>
    <h3>DONATE WITH DATA</h3>
    <p class="pow">POWERED BY GWH</p>
    <div class="mark"><i></i>Giftwell Hub</div>
    <div class="btn btn-green">Donate Data</div>
  </div>

  <div class="video" role="img" aria-label="Photo of a team meeting around a wooden table in a bright loft office">
    <div class="play"><svg width="20" height="22" viewBox="0 0 20 22"><path d="M2 1l17 10L2 21z" fill="#fff"/></svg></div>
  </div>

  <section class="enroll">
    <h2>WHY ENROLL!</h2>
    <div class="perk" style="top:140px">
      <div class="ic"><svg width="40" height="40" viewBox="0 0 40 40" fill="none" stroke="#fff" stroke-width="2"><circle cx="20" cy="20" r="14"/><circle cx="20" cy="20" r="6"/></svg></div>
      <div><h4>DROPS</h4><p>Lorem ipsum dolor sit amet, consectetur cing elit, sed do eiusmod tempor</p></div>
    </div>
    <div class="perk" style="top:260px">
      <div class="ic"><svg width="40" height="40" viewBox="0 0 40 40" fill="none" stroke="#fff" stroke-width="2"><path d="M6 14h28l-3-8H9zM8 14v20h24V14M16 34v-10h8v10"/></svg></div>
      <div><h4>MARKETPLACE</h4><p>Lorem ipsum dolor sit amet, consectetur cing elit, sed do eiusmod tempor</p></div>
    </div>
    <div class="perk" style="top:388px">
      <div class="ic"><svg width="40" height="40" viewBox="0 0 40 40" fill="none" stroke="#fff" stroke-width="2"><path d="M20 3l15 8.5v17L20 37 5 28.5v-17z"/><text x="20" y="24" fill="#fff" stroke="none" font-size="10" font-family="Poppins,sans-serif" text-anchor="middle">NFT</text></svg></div>
      <div><h4>MY NFTS</h4><p>Lorem ipsum dolor sit amet, consectetur cing elit, sed do eiusmod tempor</p></div>
    </div>
  </section>

  <section class="notify">
    <h2>GET NOTIFIED ABOUT<br>NEW AMAZING PRODUCTS</h2>
    <div class="subscribe"><span>Email address</span><b>SUBSCRIBE</b></div>
    <h3>NEVER MISS A DROB</h3>
    <p style="top:285px">Subscribe for the latest news, Drop &amp; Collectibles</p>
    <p style="top:329px">Lorem ipsum dolor sit amet, consectetur adipiscing elit, sed do eiusmod tempor incididunt ut labore et dolore magna aliqua. Ut enim ad minim veniam, quis</p>
    <p style="top:430px">Nostrud exercitation ullamco laboris nisi ut aliquip</p>
  </section>

  <p class="copy">© Copyrights 2022 Company name | All Rights Reserved</p>
</div>
</body>
</html>
```